Law Firm Profile

I need a Law firm Profile design. Something professional, corporate inspired, unique and sophisticated. Preferred colours are blue, grey and white. Completion timeline is 5 days. Details of law firm are in the uploaded document

```html
<!DOCTYPE html>
<html lang="en">
<head>
<meta charset="utf-8">
<title>KVR Advocates – Law Firm Profile</title>
<link rel="stylesheet" href="https://fonts.googleapis.com/css2?family=Tinos:ital,wght@0,400;0,700;1,400&display=swap">
<style>
  :root{
    --canvas:#e8e5e0;
    --ink:#1d1f24;
    --navy:#173f73;
    --blue:#1f5d9c;
    --sky:#9cc9f0;
    --white:#ffffff;
    --paper-warm-a:#e9e6e2;
    --paper-warm-b:#c9b8a2;
    --dark-a:#4a4744;
    --dark-b:#6b4030;
    --grey-a:#9a9a97;
    --grey-b:#5d5d5b;
    --band:rgba(70,70,70,.82);
    --frame:#111111;
  }
  *{box-sizing:border-box;margin:0;padding:0}
  html,body{width:1200px;height:900px;overflow:hidden}
  body{background:var(--canvas);font-family:"Tinos","Times New Roman",serif;color:var(--ink);position:relative}

  .page{position:absolute;overflow:hidden;box-shadow:0 4px 14px rgba(0,0,0,.22)}
  .page__photo{position:absolute;inset:0}

  /* Cover */
  .cover{left:20px;top:34px;width:280px;height:396px}
  .cover .page__photo{background:linear-gradient(160deg,#c7c7c4 0%,var(--grey-a) 45%,var(--grey-b) 100%)}
  .cover__band{position:absolute;left:0;right:0;top:282px;height:70px;background:var(--band);
    display:flex;flex-direction:column;justify-content:center;align-items:center;color:var(--white);letter-spacing:.5px}
  .cover__firm{font-size:25px;line-height:1}
  .cover__kind{font-size:17px;line-height:1.2;margin-top:3px}

  /* Back page */
  .back{left:20px;top:470px;width:280px;height:396px;text-align:center;color:var(--navy)}
  .back .page__photo{background:linear-gradient(180deg,#dfe3e8 0%,#c9ced5 40%,#e7e9ec 100%)}
  .back__body{position:relative;padding:62px 16px 0}
  .back__roles{list-style:none;font-size:9.5px;line-height:1.35;text-transform:uppercase}
  .back__heading{font-size:11px;text-transform:uppercase;margin:6px 0 2px;color:var(--navy)}
  .back__values{font-size:7.6px;line-height:1.4;color:var(--ink);margin-top:2px}
  .back__contact{font-size:7.6px;line-height:1.45;color:var(--ink)}

  /* Spread */
  .spread-left{left:340px;top:153px;width:420px;height:594px}
  .spread-left .page__photo{background:linear-gradient(165deg,#efedeb 0%,var(--paper-warm-a) 35%,#d9cdbf 70%,var(--paper-warm-b) 100%)}
  .spread-right{left:760px;top:153px;width:420px;height:594px;color:var(--white)}
  .spread-right .page__photo{background:linear-gradient(150deg,#56524f 0%,var(--dark-a) 40%,var(--dark-b) 80%,#3c2a22 100%)}
  .spread-left::after{content:"";position:absolute;top:0;right:0;bottom:0;width:18px;background:linear-gradient(90deg,transparent,rgba(0,0,0,.12))}

  .page__text{position:relative;padding:34px 22px 0;font-size:7.6px;line-height:1.36}
  .page__text p{margin-bottom:7px}
  .area{color:var(--blue);font-size:9.5px}
  .spread-right .area{color:var(--sky)}
  .section-title{color:var(--sky);font-size:10.5px;text-transform:uppercase;margin:10px 0 2px}
  .role{color:var(--sky);font-size:9px;text-transform:uppercase}
  .role span{text-transform:none;font-size:8px}

  .thumb{float:right;width:82px;height:60px;border:3px solid var(--frame);margin:0 0 6px 10px;clear:right}
  .thumb--desk{background:linear-gradient(135deg,#c9c3b6,#6f6658)}
  .thumb--meeting{background:linear-gradient(135deg,#e9eef2,#7d8791)}
  .thumb--papers{background:linear-gradient(135deg,#6b4d34,#2c2621)}
  .thumb--notes{background:linear-gradient(135deg,#3b3a3d,#d9cdb6)}
  .thumb--lens{background:linear-gradient(135deg,#f2f2f2,#8a8a8a)}
  .thumb--signing{background:linear-gradient(135deg,#2d3440,#b5926a)}
</style>
</head>
<body>

<section class="page cover" aria-label="Front cover">
  <div class="page__photo" role="img" aria-label="Wooden gavel on a grey timber desk beside an open book"></div>
  <div class="cover__band">
    <span class="cover__firm">KVR ADVOCATES</span>
    <span class="cover__kind">LAW FIRM PROFILE</span>
  </div>
</section>

<section class="page spread-left" aria-label="Practice areas">
  <div class="page__photo" role="img" aria-label="Faded photo of a lawyer's desk with papers and a gavel"></div>
  <div class="page__text">
    <div class="thumb thumb--desk" role="img" aria-label="Desk with documents, scales and a gavel"></div>
    <p><span class="area">KVR Advocates</span> is an established legal firm situated in Riverton, Westmara. The firm was founded in 2013 by Mr Samuel T Lungu S. C, the current Director of Public Prosecutions. The firm represents a wide range of clients both local and international and is dedicated to providing the highest quality of services in various areas of the law including –</p>
    <div class="thumb thumb--meeting" role="img" aria-label="Business people standing in a bright office"></div>
    <p><span class="area">Corporate Law</span> - We provide comprehensive legal services for corporate clients including in the areas of corporate governance, regulatory compliance, due diligence and risk management advisory. We seamlessly manage the legal aspects of our clients' transactions and ensure that all documentary and contractual requirements are professionally and strategically executed.</p>
    <p><span class="area">Commercial Law</span> - We have vast knowledge and experience in navigating complex commercial legal matters, including contract drafting, negotiations and compliance. We are aligned with the international environment and our lawyers keep up to date on evolving rules of international law and any applicable conflict of laws issues. Our lawyers understand the interplay between the evolving digitalization of the business environment, jurisdictional variances and the legal implications of innovations to the legal environment.</p>
    <div class="thumb thumb--papers" role="img" aria-label="Hands reviewing documents on a wooden table"></div>
    <p><span class="area">Estate and Family Law</span> - We are well versed in handling estate planning, Wills, Trusts, guardianship, divorce and probate matters to address clients' specific legal needs. Our flexible approach in implementing the full range of established dispute resolution methods at appropriate stages of the transactions and matters speaks to the successful management of even the most complex cases.</p>
    <p><span class="area">Debt Collection</span> - We efficiently handle the recovery process which is crucial for the businesses, financial institutions and individuals we represent, ensuring that disruptions and cost to our clients are mitigated.</p>
    <div class="thumb thumb--notes" role="img" aria-label="Lawyer writing notes in a book beside a laptop"></div>
    <p><span class="area">Civil and Criminal Litigation</span> - We have a notable and well respected track record in the area of litigation and all ancillary processes, we have handled major cases in commercial, criminal, constitutional and other areas of the law. We are committed to ensuring that our work is backed by meticulous legal analysis, structure and sound strategy, ensuring that we draw from the benefits of the integrated and multi-faceted nature of our practice to ensure best results for our clients.</p>
    <p><span class="area">Administrative Law</span> - We represent a significant number of clients in the area of public law and have handled a large number of judicial review matters regarding immigration and deportation matters, regulatory infringements among others. We are committed to offering comprehensive guidance, clear communication and swift and appropriate response and high quality strategy from the administrative stage, at first instance, and across all stages of the appeal process.</p>
  </div>
</section>

<section class="page spread-right" aria-label="Practice areas and key personnel">
  <div class="page__photo" role="img" aria-label="Shelf of leather-bound law books with a gavel in low light"></div>
  <div class="page__text">
    <div class="thumb thumb--lens" role="img" aria-label="Magnifying glass over a dictionary entry"></div>
    <p><span class="area">Land Law</span> - We have handled a wide range of land matters including trespass litigation, encroachment, rectifications and conveyancing and manage a substantial caseload of cases.</p>
    <p><span class="area">Constitutional Law</span> - We are a leading firm in constitutional law matters and have handled a plethora of presidential, parliamentary and local government election petitions. Our vast expertise in constitutional law is also displayed by our extensive portfolio in handling all manner of novel challenging matters in this area from constitutional interpretation to general constitutional petitions as well as motions. We have a strong database of case-law records and material which enhances our nuanced and detailed understanding of constitutional law enabling us to render well researched legal opinions to our clients.</p>
    <h2 class="section-title">Key Personnel</h2>
    <p><span class="role">Managing Partner – <span>Grace Nkonde</span></span><br>
    Grace Nkonde has more than seven years of experience in various areas of the law including commercial law, mining law, construction law, labour law, company law, constitutional law, human rights law, ICT law, administrative law, legislative drafting, civil and criminal litigation and energy law. She studied law at the Riverton University, graduated in 2015 and was admitted to the bar in 2016. Since April 2022 she has sat on the licensing committee of the Power Licensing Board and is well versed in the matters relating to the energy sector. She is a member of the Press Freedom Trust and advocates for digital rights and freedom of expression. She provides legal advisory services to various civil society organizations and undertakes strategic litigation and she holds a postgraduate diploma in legislative drafting and advocates for legislative reform and advancement in various areas of the law.</p>
    <div class="thumb thumb--signing" role="img" aria-label="Lawyer signing papers beside a gavel and scales"></div>
    <p><span class="role">Associate – <span>Ruth Tembo</span></span><br>
    Ruth Tembo has over three years of experience in civil litigation, conveyancing, handling corporate and commercial transactions, contract drafting, family law, human rights law, labour disputes, debt recovery as well as administrative law. She studied at Westmara Open University and graduated in 2016 and was admitted to the Bar in 2020. She is a member of the Public Interest Committee of the Bar Association of Westmara and has a keen interest in human rights matters.</p>
    <h2 class="section-title">Management Structure</h2>
    <p>We have a dedicated team of personnel whose primary goal is to provide the highest quality of service in compliance with all applicable rules of professional conduct. Our support team is friendly, skilled and diverse and work together to ensure that the lawyer-client relationship is seamlessly and properly managed.</p>
  </div>
</section>

<section class="page back" aria-label="Back page">
  <div class="page__photo" role="img" aria-label="Blurred courthouse facade with columns"></div>
  <div class="back__body">
    <ol class="back__roles">
      <li>1. Managing Partner</li>
      <li>2. Partner (s)</li>
      <li>3. Associate (s)</li>
    </ol>
    <h2 class="back__heading">Support Staff</h2>
    <ol class="back__roles">
      <li>4. Office Manager</li>
      <li>5. Assistant Office Manager</li>
      <li>6. Legal Clerk</li>
      <li>7. Receptionist</li>
    </ol>
    <h2 class="back__heading" style="margin-top:12px">Core Values</h2>
    <p class="back__values">We take pride in the quality of our legal services in which we incorporate our core values which include integrity, passion, credibility, continuous professional development and excellent client care in the management of our clients' instructions. The firm is regulated by the Bar Association of Westmara, and adherence to legal ethics and conduct forms the backbone of our practice and the firm's culture. We also aim to efficiently to harness creative, bespoke and expert solutions to meet every client's particular needs.</p>
    <h2 class="back__heading" style="margin-top:12px">Business Address and Contact Information</h2>
    <p class="back__contact">Plot No. 14, Kafwa Road, Hillcrest Park, Riverton, Westmara<br>
    P.O. Box 40217, Eastgate<br>
    Cell: +555 0100 201, +555 0100 202, +555 0100 203, +555 0100 204<br>
    Tell: +555 0199 300<br>
    Email: office@kvradvocates.law</p>
  </div>
</section>

</body>
</html>
```